Business Card Design Project : Ridgeline Press

In preparation for market launch, Tamarind's Ridgeline Press require the development of a business card. Ridgeline Press is a Community online publishing web portal. We provide the the city of Whistler located in B.C. (Canada) business directories, News, Classified ads, News, Events and blogs etc.

The main focus of the brand is to help local businesses to corporate with their online advertisement and marketing. Meeting our clients face to face is a must (B2B).

Target Market(s)

The target market is B2B customers. Business Owners to Marketing, advertising Managers

Industry/Entity Type

Business

Requirements
Must have
• - The business card will be two sided.
the BACK side will have our logo which consist of (icon, url,slogan) submited. The logo will be middle and centred.

The FRONT side should have company details:

Company Legal Name: TAMARIND RIDGELINE MEDIA

Owen Farsk
Director of Sales & Marketing

www.tamarindridgeline.biz
owen@tamarindridgeline.biz

Phone: 604 317 8842
#2714 - 582 E. Halvern St.
Vancouver, B.C. V7K2R4 Canada
Nice to have
• - For the "FRONT" side of our business card. You can separate or re-arrange with our logo components (icon, logo,slogan). It does not have to be together.

Also our company legal name is rather long so arrange or organize the name in a way to make it shorter. Your experience and creativity will have to come in play.
Should not have
• should not have other colors beside logo color and black text (2 colors). Also nothing Three dimensional

```html
<!DOCTYPE html>
<html lang="en">
<head>
<meta charset="utf-8">
<title>Ridgeline Press – Business Card</title>
<link rel="stylesheet" href="https://fonts.googleapis.com/css2?family=PT+Sans:wght@400;700&family=Arimo:wght@400&display=swap">
<style>
  :root {
    --brand-blue: #0b7bd0;
    --brand-blue-faint: #cfe3f5;
    --ink: #111111;
    --paper: #ffffff;
    --backdrop: #ebe7e1;
  }
  * { margin: 0; padding: 0; box-sizing: border-box; }
  html, body { width: 1200px; height: 1000px; overflow: hidden; }
  body {
    position: relative;
    background: var(--backdrop);
    font-family: "PT Sans", "Segoe UI", sans-serif;
    color: var(--ink);
  }

  .card { position: absolute; overflow: hidden; }

  /* Back side */
  .card-back {
    left: 36px; top: 37px; width: 751px; height: 443px;
    background: var(--brand-blue);
  }
  .back-brand {
    position: absolute; left: 0; right: 0; top: 150px;
    display: flex; justify-content: center; align-items: center; gap: 16px;
    color: var(--paper); font-weight: 700; font-size: 54px; line-height: 1;
  }
  .brand-dot {
    width: 30px; height: 30px; border-radius: 50%; background: var(--paper);
  }
  .back-url {
    position: absolute; left: 0; right: 0; top: 253px; text-align: center;
    font-weight: 700; font-size: 30px; color: var(--ink);
  }
  .back-slogan {
    position: absolute; left: 0; right: 0; top: 290px; text-align: center;
    font-size: 24px; color: var(--paper);
  }

  /* Front side */
  .card-front {
    left: 393px; top: 520px; width: 751px; height: 444px;
    background: var(--paper);
  }
  .front-brand {
    position: absolute; left: 80px; top: 50px;
    display: flex; align-items: center; gap: 10px;
    color: var(--brand-blue); font-weight: 700; font-size: 34px; line-height: 1;
  }
  .front-brand .brand-dot { width: 20px; height: 20px; background: var(--brand-blue); }
  .front-url {
    position: absolute; left: 24px; top: 110px;
    font-weight: 700; font-size: 22px;
  }
  .front-slogan {
    position: absolute; left: 82px; top: 137px;
    font-size: 17px; color: var(--brand-blue);
  }
  .edge-tab {
    position: absolute; width: 11px; background: var(--brand-blue);
  }
  .edge-tab-left { left: 0; top: 200px; height: 240px; border-radius: 0 10px 10px 0; }
  .edge-tab-right { right: 0; top: 113px; height: 118px; border-radius: 10px 0 0 10px; }

  .person { position: absolute; right: 28px; top: 128px; text-align: right; }
  .person-name {
    font-family: "Arimo", Arial, sans-serif;
    font-weight: 400; font-size: 46px; line-height: 1; color: var(--brand-blue);
  }
  .person-title { font-size: 19px; margin-top: 10px; }

  .address {
    position: absolute; left: 24px; top: 215px;
    font-size: 20px; line-height: 29px; font-style: normal;
  }
  .contact-list {
    position: absolute; left: 24px; top: 281px; list-style: none;
    font-size: 20px;
  }
  .contact-item { display: flex; align-items: center; gap: 6px; height: 28px; }
  .contact-item.gap-above { margin-top: 14px; }
  .contact-icon { width: 20px; height: 20px; fill: var(--brand-blue); flex: none; }

  .faint-brand {
    position: absolute; right: 30px; top: 322px;
    font-weight: 700; font-size: 40px; line-height: 1;
    color: var(--brand-blue-faint); white-space: nowrap;
  }
</style>
</head>
<body>

  <section class="card card-back" aria-label="Business card back">
    <div class="back-brand"><span class="brand-dot"></span>Ridgeline Press</div>
    <p class="back-url">www.tamarindridgeline.biz</p>
    <p class="back-slogan">Your information gateway</p>
  </section>

  <section class="card card-front" aria-label="Business card front">
    <div class="front-brand"><span class="brand-dot"></span>Ridgeline Press</div>
    <p class="front-url">www.tamarindridgeline.biz</p>
    <p class="front-slogan">Your information gateway</p>

    <span class="edge-tab edge-tab-left"></span>
    <span class="edge-tab edge-tab-right"></span>

    <div class="person">
      <h1 class="person-name">Owen Farsk</h1>
      <p class="person-title">Director of Sales &amp; Marketing</p>
    </div>

    <address class="address">
      #2714 - 582 E. Halvern St.<br>
      Vancouver, B.C. V7K2R4 Canada
    </address>

    <ul class="contact-list">
      <li class="contact-item">
        <svg class="contact-icon" viewBox="0 0 24 24" aria-hidden="true"><path d="M6.6 10.8a15.1 15.1 0 0 0 6.6 6.6l2.2-2.2a1 1 0 0 1 1-.25 11.4 11.4 0 0 0 3.6.57 1 1 0 0 1 1 1V20a1 1 0 0 1-1 1A17 17 0 0 1 3 4a1 1 0 0 1 1-1h3.5a1 1 0 0 1 1 1c0 1.250.2 2.450.57 3.57a1 1 0 0 1-.25 1z"/></svg>
        604 317 8842
      </li>
      <li class="contact-item">
        <svg class="contact-icon" viewBox="0 0 24 24" aria-hidden="true"><path d="M7 2h10a2 2 0 0 1 2 2v16a2 2 0 0 1-2 2H7a2 2 0 0 1-2-2V4a2 2 0 0 1 2-2zm0 3v12h10V5zm5 13.2a1.2 1.2 0 1 0 0 2.4 1.2 1.2 0 0 0 0-2.4z"/></svg>
        &nbsp;+00(0)0 00000000
      </li>
      <li class="contact-item gap-above">
        <svg class="contact-icon" viewBox="0 0 24 24" aria-hidden="true"><path d="M2 6a2 2 0 0 1 2-2h16a2 2 0 0 1 2 2v12a2 2 0 0 1-2 2H4a2 2 0 0 1-2-2zm2 .5V7l8 5 8-5v-.5zM4 9.3V18h16V9.3l-8 5z"/></svg>
        owen@tamarindridgeline.biz
      </li>
      <li class="contact-item">
        <svg class="contact-icon" viewBox="0 0 24 24" aria-hidden="true"><path d="M12 2a10 10 0 1 0 0 20 10 10 0 0 0 0-20zm6.9 9h-3a15.6 15.6 0 0 0-1.2-5.6A8 8 0 0 1 18.9 11zM12 4.1c.9 1.2 1.8 3.7 1.9 6.9h-3.8c.1-3.2 1-5.7 1.9-6.9zM9.3 5.4A15.6 15.6 0 0 0 8.1 11h-3a8 8 0 0 1 4.2-5.6zM5.1 13h3a15.6 15.6 0 0 0 1.2 5.6A8 8 0 0 1 5.1 13zm6.9 6.9c-.9-1.2-1.8-3.7-1.9-6.9h3.8c-.1 3.2-1 5.7-1.9 6.9zm2.7-1.3a15.6 15.6 0 0 0 1.2-5.6h3a8 8 0 0 1-4.2 5.6z"/></svg>
        www.tamarindridgeline.biz
      </li>
    </ul>

    <div class="faint-brand" aria-hidden="true">Ridgeline Press</div>
  </section>

</body>
</html>
```